Email Preference Page Design

We are looking for a 2 page design for our users to edit their email preferences and submit friend referrals. You can find the fuctionality, content and text here:

https://brightvanta.mailrelayhub.example/app/linkClick/7281/5fa9c1d3b07e442b/28374615/9bd4e01a7c3f2a65

* the shipping and billing address might be different so you need to show the billing if the "same as shipping" box is not checked. It can auto-hide like the page above shows if that fits your design.

* when the "unsubscribe from all email lists" box is selected, all the other checkbox options will hide as in the example page. We need you to show us what the site will look like with and without that checkbox selected.

We want to match these two pages to the general feel of these website pages:

www.brightvanta.com
and
free.brightvanta.com

The page should be very clean and tight. Project is for design only but must be able to be implemented in html showing button and checkbox states. Technically this must be two pages for our system - one for all the user info and one for individual email referrals (see example above).

Target Market(s)

video professionals

Industry/Entity Type

Shipping

Requirements
Must have
• our logo (see numerous versions attached)
well designed header
well designed sections
clean editable text
tight layout
html friendly
easy to understand
2 pages
Nice to have
• custom checkboxes and radio buttons

```html
<!DOCTYPE html>
<html lang="en">
<head>
<meta charset="utf-8">
<title>Communication Preferences – brightvanta</title>
<link href="https://fonts.googleapis.com/css2?family=Dosis:wght@600&family=PT+Sans:wght@400;700&display=swap" rel="stylesheet">
<style>
  :root {
    --navy: #1d2f3f;
    --page: #eceeef;
    --card: #ffffff;
    --orange: #f05a22;
    --orange-dark: #d9461a;
    --ink: #1f2f3d;
    --muted: #6b6f73;
    --field: #f2f3f4;
    --field-border: #c9cccf;
  }
  * { box-sizing: border-box; margin: 0; padding: 0; }
  html, body { width: 915px; height: 1200px; overflow: hidden; }
  body {
    position: relative;
    background: var(--page);
    font-family: "PT Sans", sans-serif;
    color: var(--ink);
  }
  .top-band { position: absolute; left: 0; top: 0; width: 915px; height: 70px; background: var(--navy); }
  .brand-tab { position: absolute; left: 242px; top: 0; width: 432px; height: 110px; }
  .brand-name {
    position: absolute; left: 0; top: 22px; width: 432px; text-align: center;
    font-size: 44px; font-weight: 400; color: var(--ink); letter-spacing: 0.5px;
    display: flex; align-items: center; justify-content: center; gap: 12px;
  }
  .brand-dot { width: 22px; height: 22px; border-radius: 50%; background: var(--orange); }
  .page-title {
    position: absolute; left: 60px; top: 132px;
    font-family: "Dosis", sans-serif; font-weight: 600; font-size: 32px;
    color: var(--orange); letter-spacing: 0.6px;
  }
  .card { position: absolute; background: var(--card); border-radius: 3px; box-shadow: 0 0 2px rgba(0,0,0,0.08); }
  .card--contact { left: 57px; top: 186px; width: 799px; height: 398px; }
  .card--filters { left: 57px; top: 605px; width: 798px; height: 493px; }
  .section-heading { position: absolute; font-weight: 400; color: var(--ink); }
  .field {
    position: absolute; height: 28px; background: var(--field);
    border: 1px solid var(--field-border); border-radius: 2px;
    font-size: 11px; color: var(--muted); padding-left: 13px; line-height: 26px;
  }
  .plus { position: absolute; font-size: 12px; color: var(--ink); }
  .check {
    position: absolute; width: 14px; height: 14px; border: 1px solid #bfc3c6;
    border-radius: 2px; background: linear-gradient(#ffffff, #eceeef);
  }
  .check--lg { width: 17px; height: 17px; }
  .label { position: absolute; font-size: 10px; color: var(--muted); white-space: nowrap; }
  .group-title { position: absolute; left: 39px; font-size: 13px; color: var(--orange); }
  .unsubscribe-label { position: absolute; font-size: 11.5px; color: var(--ink); }
  .submit-button {
    position: absolute; left: 36px; top: 423px; width: 103px; height: 33px;
    background: linear-gradient(#ff7a3d, var(--orange-dark)); border: 1px solid #c9431a;
    border-radius: 2px; color: #fff; font-family: "PT Sans", sans-serif; font-size: 18px;
  }
  .footer { position: absolute; left: 0; top: 1130px; width: 915px; height: 70px; background: var(--navy); }
  .footer-text { position: absolute; left: 0; top: 21px; width: 915px; text-align: center; font-size: 10px; color: #d5dbe0; }
</style>
</head>
<body>
  <header>
    <div class="top-band"></div>
    <svg class="brand-tab" viewBox="0 0 432 110" aria-hidden="true">
      <path d="M0 0 H432 V92 Q216 118 0 92 Z" fill="#ffffff"/>
    </svg>
    <div class="brand-tab">
      <div class="brand-name"><span class="brand-dot"></span>brightvanta</div>
    </div>
  </header>

  <h1 class="page-title">Communication Preferences</h1>

  <section class="card card--contact">
    <h2 class="section-heading" style="left:29px;top:20px;font-size:21px;">Contact Information</h2>
    <div class="field" style="left:29px;top:56px;width:228px;">First Name</div>
    <div class="field" style="left:270px;top:56px;width:227px;">Last Name</div>
    <div class="field" style="left:29px;top:94px;width:228px;">Phone no.</div>
    <div class="field" style="left:270px;top:94px;width:227px;">Email address</div>
    <div class="field" style="left:29px;top:132px;width:228px;">Address &nbsp;1</div>
    <div class="field" style="left:270px;top:132px;width:227px;">Address 2</div>
    <div class="field" style="left:29px;top:172px;width:228px;">Address 3</div>
    <div class="field" style="left:270px;top:172px;width:227px;">City</div>
    <div class="field" style="left:29px;top:210px;width:228px;">Country</div>
    <div class="field" style="left:270px;top:210px;width:227px;">State</div>
    <div class="field" style="left:29px;top:248px;width:149px;">Postal Code + 4</div>
    <span class="plus" style="left:189px;top:254px;">+</span>
    <div class="field" style="left:201px;top:248px;width:53px;"></div>
    <span class="check check--lg" style="left:30px;top:294px;"></span>
    <span class="label" style="left:55px;top:297px;">Subscribe me to your general email list &nbsp;This monthly email includes free video loops and VIP sale notices</span>

    <h2 class="section-heading" style="left:533px;top:33px;font-size:18px;">Shipping Address</h2>
    <span class="check check--lg" style="left:535px;top:64px;"></span>
    <span class="label" style="left:559px;top:66px;">Billing address is same as shipping address</span>
    <div class="field" style="left:533px;top:93px;width:237px;">Street Address 1</div>
    <div class="field" style="left:533px;top:135px;width:237px;">Street Address 2</div>
    <div class="field" style="left:533px;top:172px;width:237px;">Street Address 3</div>
    <div class="field" style="left:533px;top:210px;width:237px;">City</div>
    <div class="field" style="left:533px;top:247px;width:237px;">Country</div>
    <div class="field" style="left:533px;top:287px;width:237px;">State</div>
    <div class="field" style="left:533px;top:325px;width:160px;">Postal Code + 4</div>
    <span class="plus" style="left:704px;top:331px;">+</span>
    <div class="field" style="left:717px;top:325px;width:53px;"></div>
  </section>

  <section class="card card--filters">
    <h2 class="section-heading" style="left:38px;top:30px;font-size:21px;">Help us filter our emails so we are only sending relevant information to you.</h2>

    <h3 class="group-title" style="top:69px;font-weight:400;">Send me emails about these product types:</h3>
    <span class="check" style="left:40px;top:96px;"></span><span class="label" style="left:61px;top:96px;">Low energy motion loops</span>
    <span class="check" style="left:40px;top:119px;"></span><span class="label" style="left:61px;top:119px;">High energy motion loops</span>
    <span class="check" style="left:40px;top:143px;"></span><span class="label" style="left:61px;top:143px;">Timelapse footage</span>
    <span class="check" style="left:40px;top:167px;"></span><span class="label" style="left:61px;top:167px;">Worship or wedding motion loops</span>
    <span class="check" style="left:40px;top:190px;"></span><span class="label" style="left:61px;top:190px;">Pre-mixed DVDs and BluRay</span>
    <span class="check" style="left:317px;top:96px;"></span><span class="label" style="left:338px;top:95px;">Entertainment lasers for concerts and clubs</span>
    <span class="check" style="left:317px;top:119px;"></span><span class="label" style="left:338px;top:118px;">Entertainment lasers for text &amp; logo display</span>
    <span class="check" style="left:317px;top:143px;"></span><span class="label" style="left:338px;top:142px;">Custom logo animation services</span>
    <span class="check" style="left:317px;top:167px;"></span><span class="label" style="left:338px;top:165px;">Video software for creating video animations</span>
    <span class="check" style="left:317px;top:190px;"></span><span class="label" style="left:338px;top:189px;">Video software for live performance (Vjing)</span>

    <h3 class="group-title" style="top:227px;font-weight:400;">I am Involved in or have interest in:</h3>
    <span class="check" style="left:40px;top:256px;"></span><span class="label" style="left:61px;top:256px;">VJing (live performance video)</span>
    <span class="check" style="left:40px;top:280px;"></span><span class="label" style="left:61px;top:280px;">DJing (live performance audio+video)</span>
    <span class="check" style="left:40px;top:303px;"></span><span class="label" style="left:61px;top:303px;">Performing in a band</span>
    <span class="check" style="left:40px;top:327px;"></span><span class="label" style="left:61px;top:327px;">Video editing</span>
    <span class="check" style="left:40px;top:350px;"></span><span class="label" style="left:61px;top:350px;">Corporate presentations</span>
    <span class="check" style="left:317px;top:256px;"></span><span class="label" style="left:338px;top:255px;">Worship video services</span>
    <span class="check" style="left:317px;top:280px;"></span><span class="label" style="left:338px;top:279px;">Lasers for entertainment &amp; branding</span>
    <span class="check" style="left:317px;top:303px;"></span><span class="label" style="left:338px;top:302px;">Special offers from BrightVanta partners</span>

    <span class="check" style="left:38px;top:390px;"></span>
    <span class="unsubscribe-label" style="left:61px;top:389px;">Unsubscribe from all email lists</span>

    <button class="submit-button" type="button">Submit</button>
  </section>

  <footer class="footer">
    <p class="footer-text">All Rights Reserved Copyright© 2013 - BrightVanta</p>
  </footer>
</body>
</html>
```